Systems and Technology Consultants - Website

Design & Build a website for a new company which operates in the Systems and Technology space for Transportation, Government and Commercial sectors.

Overall design should be minimalist in nature.
Should also have a feed that provides news and event updates on the main page.
Logo has already been awarded and should be incorporated into the site.

We like the overall layout, functionality and simplicity of the below sites. Submitted designs could be similar to or a combination of the aspects on these sites, or perhaps a whole different concept - we are open to new ideas.
Norvique.com
Teblo.it

Update 1 Dated 27 May 2014

All I am moving away from the Teblo.it website and would like it to be more aligned with Norvique.com not only in layout but in functionality. I will be extending the deadline of this design brief for two weeks to incorporate additional requirements and will add addtional funding to the project.

Apologies for not having more information available to provide but with so many submissions its getting confusing.

Thanks Derek

Please note that the brief has been updated and the deadline has been extended.

Important: We will need two language versions of the website, English and Arabic; the website is hosted on HostPelican

Hello All, Thank you for your submissions. We have narrowed it down to the final 6 designers and I just wanted to take a moment and provide a bit of feedback regarding the concepts that we like and the modifications we are looking for. First, let me mention some of the design functions we like. - At the top of the homepage we really like the "region" or "language" tab so that the website can be viewed in both English and Arabic. - We like the homepage to have clear color variation so that the different sections of the homepage are distinct. Additionally, we like the bottom portion of the homepage to be in red. We feel that draws attention to our contact information. Again, we would like the colors to integrate black, gray-scale, red, etc. - Having a search tab at the top of the home page, or integrated into the main image, so that the site is easy to navigate. - We especially like the main image to have the scrolling tabs at the bottom so it is easy to browse the services offered (Consultancy, Solutions Architecture, Masters Systems Integration, Independent Design Review). - In regards to the services offered tab we really like the idea that a few people presented that have the outside of our logo with an icon in the middle of consultancy, solutions, etc., etc. Secondly, as mentioned in our brief we really enjoy the design of norvique site. Specially, we enjoy the strong iconic images they use, the way the tabs at the top scroll easily, and contact us page that generates an email. Lastly, I've included some photos of the concept we have been working on. What we are trying to demonstrate is how our company offers a range of services that are essentially linked together. We provide individual services that when combined present the full service package. We would like this concept to be integrated into the over concept of our website. Please feel free to ask for clarification of any of the above points or contact us if you have any additional questions. We appreciate all of your hard work and are very excited to see the updated designs. Best, Marta Vennick Quelbrant Senior Program Manager marta.vennick@quelbrant-example.com

Industry/Entity Type

Government

Font styles to use
Serif
Sans Serif

Requirements
Must have
• Must work on/adapt to various/mobile devices (responsive)
Must be simple and straightforward
Colors should be in line/matching with logo
2 language versions: English and Arabic (no Thai)
Services should be the first group/row of items after/below the main image
Note: the website will be hosted by hostpelican
Nice to have
• Submit feedback form
What's New section
The banner at the bottom of the site should not be too large; we would like a narrow one more
It would be nice if the header/top banner (with Home, About, etc. tabs) could stay in place as you scroll down (like Norvique and Chatterloop)
We will likely only use one image with a Company slogan on the Home page rather than a carousel of images to rotate through
Should not have
• This is the existing website: http://www.quelbrant-example.org
We do not like the animation, the way the banner icons/titles bounce
Not simple enough, we don't like the functionality or how pages load so slowly
We do not like the logo centered - it should be at the left
The banner and its tabs should not be towards the right, we would like them to be centered, to go all the way across and to be below the logo

```html
<!DOCTYPE html>
<html lang="en">
<head>
<meta charset="utf-8">
<title>Kestrava International</title>
<link rel="stylesheet" href="https://fonts.googleapis.com/css2?family=Montserrat:wght@400;500;600;700&family=Open+Sans:wght@300;400;600;700&family=Lato:wght@300;400;700&display=swap">
<style>
:root{
  --red:#d8262b;
  --red-dark:#c82126;
  --ink:#1c1f24;
  --text:#333;
  --muted:#6b6b6b;
  --panel:#f5f5f5;
  --line:#dcdcdc;
  --charcoal:#3b3b3d;
  --footer-dark:#171717;
  --white:#fff;
  --orange:#e8572a;
}
*{margin:0;padding:0;box-sizing:border-box}
html,body{width:994px;height:1200px;overflow:hidden;background:var(--white)}
body{position:relative;font-family:"Open Sans",sans-serif;color:var(--text)}
.abs{position:absolute}
ul{list-style:none}

/* header */
.site-header{position:absolute;left:0;top:0;width:994px;height:116px;border-bottom:4px solid var(--red);background:var(--white)}
.brand{position:absolute;left:90px;top:26px;display:flex;align-items:center;gap:12px;color:var(--red);font-family:"Montserrat",sans-serif;font-weight:600}
.brand-square{width:40px;height:40px;background:var(--red)}
.brand-name{font-size:20px;letter-spacing:5px;line-height:22px}
.brand-sub{font-size:9px;letter-spacing:3px;line-height:12px}
.search{position:absolute;left:529px;top:25px;width:233px;height:29px;border:1px solid #cfcfcf;font-size:9.5px;color:#666;padding:7px 20px}
.search-btn{position:absolute;left:770px;top:31px}
.lang{position:absolute;left:802px;top:30px;display:flex;align-items:center;gap:8px;font-family:"Lato",sans-serif;font-size:13px;color:#555}
.lang-globe{width:28px;height:16px;border-radius:50%;background:var(--red)}
.main-nav{position:absolute;right:92px;top:78px;display:flex;gap:23px;font-family:"Montserrat",sans-serif;font-size:11.5px;font-weight:500;color:var(--ink)}
.main-nav .active{color:var(--red)}

/* hero */
.hero{position:absolute;left:0;top:116px;width:994px;height:369px;overflow:hidden}
.hero-photo{position:absolute;inset:0;background:linear-gradient(180deg,#5d5c66 0%,#3d3c48 45%,#2b2a36 100%)}
.hero-title{position:absolute;left:89px;top:106px;font-family:"Montserrat",sans-serif;font-weight:600;font-size:33px;letter-spacing:2px;line-height:44px;color:var(--white)}
.hero-title .accent{color:var(--red)}
.hero-lead{position:absolute;left:94px;top:196px;font-size:20px;font-weight:300;line-height:23px;color:var(--white)}
.hero-lead strong{color:var(--red);font-weight:700}
.btn-more{position:absolute;left:92px;top:265px;width:157px;height:32px;background:var(--red);color:var(--white);font-family:"Montserrat",sans-serif;font-weight:700;font-size:11px;letter-spacing:2px;display:flex;align-items:center;padding-left:19px;gap:16px}
.bubble{position:absolute;border-radius:50%}
.bubble-dark{left:563px;top:94px;width:66px;height:66px;background:#333}
.bubble-red{left:754px;top:14px;width:108px;height:108px;background:var(--red);color:var(--white);padding:34px 0 0 19px}
.bubble-red h3{font-family:"Montserrat",sans-serif;font-weight:700;font-size:14px;letter-spacing:2px}
.bubble-red p{font-size:11px;margin-top:1px}
.bubble-main{left:594px;top:60px;width:228px;height:228px;background:var(--white);padding:50px 0 0 43px}
.bubble-main h3{font-family:"Montserrat",sans-serif;font-weight:700;font-size:23px;letter-spacing:3px;color:var(--red)}
.bubble-main p{font-size:11px;line-height:19px;color:#333;width:170px;margin-top:6px}
.bubble-grey{left:695px;top:198px;width:108px;height:108px;background:var(--charcoal);color:var(--white);text-align:center;padding-top:31px}
.bubble-grey h4{font-family:"Montserrat",sans-serif;font-weight:700;font-size:9.5px;letter-spacing:1.5px}
.bubble-grey p{font-size:11px;line-height:19px;margin-top:3px}
.bubble-small{left:579px;top:251px;width:42px;height:42px;background:var(--white)}
.dots{position:absolute;left:489px;top:336px;display:flex;gap:9px;align-items:center}
.dots span{width:8px;height:8px;border-radius:50%;background:var(--white)}
.dots .on{width:14px;height:14px;background:var(--red)}

/* services tabs */
.service-tabs{position:absolute;left:93px;top:516px;width:809px;height:41px;border-bottom:1px solid var(--line)}
.tab{position:absolute;top:0;height:41px;border:1px solid var(--line);background:#ececec;font-family:"Lato",sans-serif;font-size:14px;color:#222;display:flex;align-items:center;justify-content:center}
.tab.current{background:var(--white);border-bottom-color:var(--white)}
.service-panel{position:absolute;left:93px;top:566px;width:809px;height:151px;background:linear-gradient(90deg,#f3f3f3,#f7f7f7)}
.service-icon{position:absolute;left:17px;top:22px;width:132px;height:89px;border-radius:44px;background:#8d8d8d}
.service-title{position:absolute;left:164px;top:17px;font-family:"Montserrat",sans-serif;font-weight:400;font-size:22px;letter-spacing:1px;color:var(--red)}
.service-text{position:absolute;left:167px;top:49px;width:630px;font-family:"Lato",sans-serif;font-size:11.5px;line-height:19px;color:#222}

/* feeds */
.section-title{position:absolute;font-family:"Montserrat",sans-serif;font-weight:500;font-size:23px;letter-spacing:1px;color:var(--ink)}
.rule{position:absolute;height:1px;background:var(--line)}
.news-title{position:absolute;left:93px;top:803px;font-family:"Montserrat",sans-serif;font-size:18px;color:var(--red)}
.news-date{position:absolute;left:93px;top:832px;font-size:9.5px;color:#555}
.news-text{position:absolute;left:93px;top:859px;width:437px;font-family:"Lato",sans-serif;font-weight:300;font-size:12.5px;line-height:17.5px;color:#555}
.more-link{position:absolute;font-family:"Lato",sans-serif;font-size:11px;color:var(--orange)}
.works{position:absolute;left:568px;top:812px;width:310px;font-family:"Lato",sans-serif;font-weight:300;font-size:12.5px;line-height:14.5px;color:#444}
.works li{position:relative;padding-left:21px;margin-bottom:6px}
.works li::before{content:"\2192";position:absolute;left:0;top:0;font-size:11px;color:#555}

/* footer */
.site-footer{position:absolute;left:0;top:970px;width:994px;height:190px;background:var(--red);color:var(--white)}
.footer-brand{position:absolute;left:88px;top:24px;display:flex;align-items:center;gap:12px;font-family:"Montserrat",sans-serif;font-weight:600}
.footer-brand .brand-square{background:var(--white);width:36px;height:36px}
.footer-about{position:absolute;left:93px;top:95px;width:250px;font-size:11px;line-height:17px}
.footer-head{position:absolute;font-family:"Open Sans",sans-serif;font-size:12.5px;font-weight:400}
.sitemap{position:absolute;left:358px;top:62px;font-size:8.5px;font-weight:700;line-height:16.6px}
.events{position:absolute;left:487px;top:62px;font-size:11px;line-height:22.5px}
.events li,.contact li{display:flex;align-items:center;gap:10px}
.contact{position:absolute;left:712px;top:60px;font-family:"Lato",sans-serif;font-size:11px;font-weight:700;line-height:25.5px}
.contact .indent{padding-left:25px}
.bottom-bar{position:absolute;left:0;top:1160px;width:994px;height:40px;background:var(--footer-dark);color:#ddd;font-size:11px}
.copyright{position:absolute;left:86px;top:12px}
.follow{position:absolute;left:759px;top:10px;font-family:"Lato",sans-serif;font-size:13px;display:flex;align-items:center;gap:8px}
.follow .social{width:20px;height:20px;border-radius:50%;background:#555}
.follow .gap{width:6px}
</style>
</head>
<body>

<header class="site-header">
  <div class="brand">
    <span class="brand-square"></span>
    <div>
      <div class="brand-name">KESTRAVA</div>
      <div class="brand-sub">INTERNATIONAL</div>
    </div>
  </div>
  <div class="search">Search Here ...............</div>
  <svg class="search-btn" width="16" height="16" viewBox="0 0 16 16"><circle cx="6.5" cy="6.5" r="5" fill="none" stroke="#bbb" stroke-width="2"/><line x1="10" y1="10" x2="14.5" y2="14.5" stroke="#bbb" stroke-width="2.4"/></svg>
  <div class="lang"><span class="lang-globe"></span><span>English</span>
    <svg width="9" height="8" viewBox="0 0 9 8"><path d="M0 0h9L4.5 8z" fill="var(--red)"/></svg>
  </div>
  <nav class="main-nav">
    <span class="active">HOME</span><span>ABOUT US</span><span>BUSINESS UNITS</span><span>SERVICES</span><span>LOCATIONS</span><span>CONTACT US</span>
  </nav>
</header>

<section class="hero">
  <div class="hero-photo" role="img" aria-label="Dusky city skyline photograph"></div>
  <h1 class="hero-title">INTEGRATED <span class="accent">SYSTEMS</span><br>RELIABLE SOLUTIONS</h1>
  <p class="hero-lead"><strong>QUELBRANT</strong> Specializes in delivering quality<br>fessional Services and Technical Projects that</p>
  <div class="btn-more">LEARN MORE
    <svg width="24" height="12" viewBox="0 0 24 12"><path d="M2 1l6 5-6 5M12 1l6 5-6 5" fill="none" stroke="#fff" stroke-width="1.5"/></svg>
  </div>
  <div class="bubble bubble-dark"></div>
  <div class="bubble bubble-red"><h3>SYSTEM</h3><p>Sitquet amer lip</p></div>
  <div class="bubble bubble-main">
    <h3>SOLUTIONS</h3>
    <p>quelbrant specializes in delivering quality professional services and technical projects that support larger .</p>
  </div>
  <div class="bubble bubble-grey"><h4>INTEGRATION</h4><p>quelbrant<br>specializes</p></div>
  <div class="bubble bubble-small"></div>
  <div class="dots"><span></span><span></span><span class="on"></span></div>
</section>

<section>
  <div class="service-tabs">
    <div class="tab current" style="left:0;width:174px">Consultancy</div>
    <div class="tab" style="left:178px;width:184px">Solutions Architecure</div>
    <div class="tab" style="left:367px;width:172px">Master Systems</div>
  </div>
  <div class="service-panel">
    <div class="service-icon" role="img" aria-label="Grey illustration of a team of people in a cloud"></div>
    <h2 class="service-title">Sitquetamet dolor Ipsum amet</h2>
    <p class="service-text">quelbrant specializes in delivering quality professional services and technical projects that support larger business goals.&nbsp; systems are tools that support a greater business function and need. we understand that most t echnical projects are conceptualized to support a larger vision with actual business goals in mind and ensure that all of our professional and certified expertise is included in our professional services to meet those goals.</p>
  </div>
</section>

<section>
  <h2 class="section-title" style="left:95px;top:753px">Latest News</h2>
  <div class="rule" style="left:90px;top:790px;width:433px"></div>
  <h3 class="news-title">Coraz mniej serwerów, coraz więcej chmury</h3>
  <div class="news-date">31 stycznia 2014</div>
  <p class="news-text">Według Vantira, szefowie IT coraz szybciej przesiadają się do chmury obliczeniow między 25-30% wszystkich sprzedanych serwerów trafi nie do korporacyjnych..</p>
  <div class="more-link" style="left:93px;top:908px">Czytaj więcej &#8594;</div>

  <h2 class="section-title" style="left:585px;top:753px">Featured Works</h2>
  <div class="rule" style="left:568px;top:790px;width:314px"></div>
  <ul class="works">
    <li>Nasi eksperci publikują na ChmuraBlog: Halden Flex System – integracja z Norvex vSpan</li>
    <li>UE: 2,5 mln nowych miejsc pracy dzięki chmurze?</li>
    <li>E-seminarium: Zwiększania efektywności biznesu poprzez zastosowanie chmury obliczeniowej</li>
  </ul>
  <div class="rule" style="left:568px;top:908px;width:321px"></div>
  <div class="more-link" style="left:568px;top:931px">Wszystkie aktualności &#8594;</div>
</section>

<footer class="site-footer">
  <div class="footer-brand">
    <span class="brand-square"></span>
    <div>
      <div class="brand-name">KESTRAVA</div>
      <div class="brand-sub">INTERNATIONAL</div>
    </div>
  </div>
  <p class="footer-about">Lorem ipsum dolorSit amet consecteturAdipsic-ing elit,ed do euismodTempor incidunt Labore et dolorMagna aliqua.Lorem ipsum dolorSit amet consecteturAdipsicing elit,</p>

  <h4 class="footer-head" style="left:351px;top:33px">SITE MAP</h4>
  <ul class="sitemap">
    <li>HOME</li><li>ABOUT US</li><li>BUSINESS UNITS</li><li>SERVICES</li><li>LOCATIONS</li><li>CONTACT US</li>
  </ul>

  <h4 class="footer-head" style="left:484px;top:33px">UP COMING EVENTS</h4>
  <ul class="events">
    <li><svg width="13" height="13" viewBox="0 0 13 13"><circle cx="6.5" cy="6.5" r="5.5" fill="none" stroke="#fff" stroke-width="1.3"/><path d="M6.5 3.5v3h2.5" fill="none" stroke="#fff" stroke-width="1.3"/></svg>Monday 07:00 AM — 07:00 PM</li>
    <li><svg width="13" height="13" viewBox="0 0 13 13"><circle cx="6.5" cy="6.5" r="5.5" fill="none" stroke="#fff" stroke-width="1.3"/><path d="M6.5 3.5v3h2.5" fill="none" stroke="#fff" stroke-width="1.3"/></svg>Tuesday 07:00 AM — 07:00 PM</li>
    <li><svg width="13" height="13" viewBox="0 0 13 13"><circle cx="6.5" cy="6.5" r="5.5" fill="none" stroke="#fff" stroke-width="1.3"/><path d="M6.5 3.5v3h2.5" fill="none" stroke="#fff" stroke-width="1.3"/></svg>Wednesday 07:00 AM — 07:00 PM</li>
    <li><svg width="13" height="13" viewBox="0 0 13 13"><circle cx="6.5" cy="6.5" r="5.5" fill="none" stroke="#fff" stroke-width="1.3"/><path d="M6.5 3.5v3h2.5" fill="none" stroke="#fff" stroke-width="1.3"/></svg>Thursday 07:00 AM — 07:00 PM</li>
  </ul>

  <h4 class="footer-head" style="left:712px;top:28px">OUR CONTACT INFORMATION</h4>
  <ul class="contact">
    <li><svg width="12" height="14" viewBox="0 0 12 14"><path d="M6 0a5 5 0 0 1 5 5c0 4-5 9-5 9S1 9 1 5a5 5 0 0 1 5-5z" fill="#fff"/><circle cx="6" cy="5" r="1.8" fill="var(--red)"/></svg>&nbsp;Kestrava International</li>
    <li class="indent">88, Orchard Lane Westbury NY</li>
    <li><svg width="12" height="14" viewBox="0 0 12 14"><rect x="2" y="0.7" width="8" height="12.6" rx="1.2" fill="none" stroke="#fff" stroke-width="1.4"/><rect x="5" y="10.5" width="2" height="1.2" fill="#fff"/></svg>&nbsp;(555) 014 27 90</li>
    <li><svg width="15" height="12" viewBox="0 0 15 12"><rect x="0.5" y="1" width="14" height="10" fill="#fff"/><path d="M3 5h9M3 8h6" stroke="var(--red)" stroke-width="1.2"/></svg>&nbsp;info@kestrava-example.com</li>
  </ul>
</footer>

<div class="bottom-bar">
  <div class="copyright">Copyrights © 2014Kestrava.com - All Rights Reserved</div>
  <div class="follow">Follow Us <span class="gap"></span><span class="social"></span><span class="social"></span><span class="social"></span></div>
</div>

</body>
</html>
```